Business cards for Harbourline Supply Pty Ltd that import building products into Australia from China
Target Market(s)
Business to Business
Industry/Entity Type
Business
Contact Information for Business Card
Front: Logo and Business Name
Rear:
Desmond Varrick
General Manager
Mobile: 0427 561 394
email: dessie@harbourlinesupply.com.au
alternative email: dessie@outbackworks.com.au
web: www.harbourlinesupply.com.au
Geelong, Townsville and Perth
Colors
ec1f27
fbee3d

```html
<!DOCTYPE html>
<html lang="en">
<head>
<meta charset="utf-8">
<title>Harbourline Supply Pty Ltd – Business Cards</title>
<link rel="stylesheet" href="https://fonts.googleapis.com/css2?family=Open+Sans:wght@400;600;700&display=swap">
<style>
  :root {
    --brand-red: #ec1f27;
    --brand-yellow: #fbee3d;
    --ink: #1d1d1d;
    --card-dark: #232323;
    --card-light: #ffffff;
    --rule: #8a8a8a;
    --backdrop: #ece9e4;
  }
  * { margin: 0; padding: 0; box-sizing: border-box; }
  html, body {
    width: 1200px; height: 900px; overflow: hidden;
    background: var(--backdrop);
    font-family: "Open Sans", Arial, sans-serif;
  }
  .canvas { position: relative; width: 1200px; height: 900px; }

  .card {
    position: absolute;
    width: 560px; height: 320px;
    border-radius: 3px;
    box-shadow: 0 6px 18px rgba(0,0,0,0.18);
  }

  /* Front: dark card with business name */
  .card--front {
    left: 110px; top: 100px;
    background: var(--card-dark);
    display: flex; align-items: center; justify-content: center;
  }
  .brand { display: flex; align-items: center; gap: 12px; }
  .brand__mark { width: 22px; height: 22px; background: var(--brand-red); flex: none; }
  .brand__name { font-weight: 700; font-size: 26px; letter-spacing: -0.2px; }
  .card--front .brand__name { color: var(--card-light); }

  /* Rear: white card with contact details */
  .card--rear {
    left: 530px; top: 470px;
    background: var(--card-light);
    display: flex; align-items: center;
    padding: 0 30px 0 34px;
  }
  .card--rear .brand { width: 240px; }
  .card--rear .brand__mark { width: 16px; height: 16px; }
  .card--rear .brand__name { color: var(--ink); font-size: 19px; line-height: 1.15; }
  .divider {
    width: 1px; height: 200px; background: var(--rule);
    margin: 0 20px 0 14px;
  }
  .contact { color: var(--ink); }
  .contact__name { font-size: 17px; font-weight: 700; letter-spacing: 0.3px; line-height: 1.1; }
  .contact__surname { color: var(--brand-red); }
  .contact__title { font-size: 12px; margin: 2px 0 14px 10px; }
  .contact__list { list-style: none; margin-left: 10px; }
  .contact__item {
    display: flex; align-items: center; gap: 8px;
    font-size: 12px; line-height: 19px;
  }
  .icon { width: 11px; height: 11px; flex: none; fill: var(--brand-red); }
  .contact__region { font-size: 12.5px; margin: 14px 0 0 10px; }
</style>
</head>
<body>
<main class="canvas">

  <section class="card card--front" aria-label="Card front">
    <div class="brand">
      <span class="brand__mark"></span>
      <span class="brand__name">Harbourline Supply Pty Ltd</span>
    </div>
  </section>

  <section class="card card--rear" aria-label="Card rear">
    <div class="brand">
      <span class="brand__mark"></span>
      <span class="brand__name">Harbourline Supply Pty Ltd</span>
    </div>
    <div class="divider"></div>
    <div class="contact">
      <p class="contact__name">DESMOND <span class="contact__surname">VARRICK</span></p>
      <p class="contact__title">General Manager</p>
      <ul class="contact__list">
        <li class="contact__item">
          <svg class="icon" viewBox="0 0 12 12" aria-hidden="true"><path d="M3 0h6a1 1 0 0 1 1 1v10a1 1 0 0 1-1 1H3a1 1 0 0 1-1-1V1a1 1 0 0 1 1-1zm0 1.5v8h6v-8zM5 10.2h2v.8H5z"/></svg>
          0427 561 394
        </li>
        <li class="contact__item">
          <svg class="icon" viewBox="0 0 12 12" aria-hidden="true"><path d="M0 2h12v8H0zm1.2 1.2v.4L6 6.8l4.8-3.2v-.4z"/></svg>
          dessie@harbourlinesupply.com.au
        </li>
        <li class="contact__item">
          <svg class="icon" viewBox="0 0 12 12" aria-hidden="true"><path d="M0 2h12v8H0zm1.2 1.2v.4L6 6.8l4.8-3.2v-.4z"/></svg>
          dessie@outbackworks.com.au
        </li>
        <li class="contact__item">
          <svg class="icon" viewBox="0 0 12 12" aria-hidden="true"><circle cx="6" cy="6" r="6"/><path d="M1 6h10M6 1v10" stroke="#fff" stroke-width="0.9"/><ellipse cx="6" cy="6" rx="2.4" ry="5" fill="none" stroke="#fff" stroke-width="0.9"/></svg>
          www.harbourlinesupply.com.au
        </li>
      </ul>
      <p class="contact__region">Geelong, Townsville and Perth</p>
    </div>
  </section>

</main>
</body>
</html>
```